Vantor Wear and Fuel is looking for a Clothing/Supplement Online Store Website!

Must be convenient, and user friendly, with vibrant colors that catch the eye!

Target Market(s)

Athletes, and Fashion Customers

Industry/Entity Type

Fitness

Coding

Coded - Design and coding required

Number of Pages Required

3 page

Font styles to use
Decorative

Colors

Designer to choose colors to be used in the design.

Requirements
Must have
• Somewhere to feature products, features to promote discounts and make announcements.
Nice to have
• My logos on each page

```html
<!DOCTYPE html>
<html lang="en">
<head>
<meta charset="utf-8">
<title>Vantor Wear and Fuel</title>
<link href="https://fonts.googleapis.com/css2?family=Mulish:wght@400;600;700;800&display=swap" rel="stylesheet">
<style>
:root{
  --ink:#333333;
  --muted:#777777;
  --topbar:#4a4a4a;
  --navbar:#ececec;
  --line:#d4d4d4;
  --card:#f5f5f5;
  --section:#efefef;
  --dark:#0b0b0b;
  --btn:#4d4d4d;
  --white:#ffffff;
}
*{box-sizing:border-box;margin:0;padding:0}
html,body{width:1200px;height:4048px;overflow:hidden;background:var(--white)}
body{font-family:'Mulish',sans-serif;color:var(--ink)}
.page{position:relative;width:1200px;height:4048px;overflow:hidden}
.abs{position:absolute}

/* top bar */
.topbar{left:0;top:0;width:1200px;height:41px;background:var(--topbar);color:#eee;font-size:12px}
.topbar .item{position:absolute;top:13px;display:flex;align-items:center;gap:5px}
.topbar .sep{position:absolute;top:6px;width:1px;height:29px;background:#666}
.topbar svg{width:11px;height:11px;fill:#eee}

/* header */
.crest{left:500px;top:0;width:200px;height:133px}
.brandmark{font-weight:800;letter-spacing:2px;color:var(--ink)}
.header-logo{left:500px;top:46px;width:200px;text-align:center;font-size:40px}
.search{left:207px;top:64px;display:flex;align-items:center;gap:10px;font-size:13px}
.round-icon{width:48px;height:48px;border-radius:50%;background:var(--topbar);display:flex;align-items:center;justify-content:center;border:3px solid #cfcfcf}
.round-icon svg{width:22px;height:22px;fill:none;stroke:#fff;stroke-width:2.2}
.search b,.cart b{font-weight:600;display:block;line-height:18px}
.search span{color:#555}
.cart{left:828px;top:64px;display:flex;align-items:center;gap:10px;font-size:13px}
.cart strong{font-weight:700}

/* nav */
.nav{left:0;top:140px;width:1200px;height:45px;background:var(--navbar);font-size:17px;color:#555}
.nav a{position:absolute;top:11px;text-decoration:none;color:inherit;white-space:nowrap}

/* hero */
.hero{left:0;top:185px;width:1200px;height:613px;clip-path:polygon(0 0,100% 0,100% 498px,50% 100%,0 498px);
  background:radial-gradient(ellipse at 68% 45%,#5a6270 0%,#2e3642 35%,#141a24 70%,#0a0e15 100%)}
.hero-edge{left:0;top:670px;width:1200px;height:136px}
.hero-logo{left:90px;top:300px;font-size:62px;color:var(--white)}
.hero-text{left:89px;top:383px;width:460px;color:var(--white);font-size:22px;line-height:36px}
.btn{position:absolute;display:flex;align-items:center;justify-content:center;gap:8px;color:var(--white);background:var(--btn);font-weight:600;text-transform:uppercase}
.hero-btn{left:90px;top:468px;width:204px;height:58px;border-radius:29px;font-size:17px}
.dots{left:90px;top:555px;display:flex;gap:8px}
.dots i{width:14px;height:14px;border-radius:50%;background:#fff;display:block}
.dots i.on{background:transparent;border:3px solid #ccc}

/* features */
.feature{top:842px;width:249px;height:66px;border:2px solid #dcdcdc;border-radius:33px;display:flex;align-items:center;gap:12px;padding-left:4px}
.feature .round-icon{width:56px;height:56px;border-width:0;box-shadow:0 0 0 3px #ddd}
.feature .round-icon svg{width:26px;height:26px}
.feature b{display:block;font-size:13px;font-weight:600;color:var(--ink)}
.feature span{font-size:12px;color:#999}

/* products */
.section-title{left:0;width:1200px;text-align:center;font-size:36px;font-weight:600;color:#4a4a4a;letter-spacing:.5px}
.card{width:251px;height:355px;background:var(--card)}
.card-name{width:251px;text-align:center;font-size:20px;color:#333}
.card-price{width:251px;text-align:center;font-size:15px;font-weight:700;color:#222}

/* apparel banner */
.apparel{left:0;top:1527px;width:1200px;height:517px;
  background:linear-gradient(90deg,#6c7478 0%,#8d9396 30%,#a7a9a8 50%,#9ea2a1 75%,#8a8f8f 100%)}
.apparel-title{left:90px;top:1652px;font-size:48px;font-weight:600;color:#3a3a3a}
.apparel-text{left:89px;top:1728px;width:470px;font-size:17px;line-height:30px;font-weight:600;color:#2a2a2a}
.apparel-btn{left:90px;top:1833px;width:175px;height:46px;font-size:17px;font-weight:500}

/* new arrivals */
.arrivals-bg{left:0;top:2044px;width:1200px;height:563px;background:var(--section)}

/* supplement */
.supplement{left:0;top:2607px;width:1200px;height:517px;background:var(--dark)}
.supplement-photo{left:0;top:2607px;width:720px;height:517px;
  background:radial-gradient(ellipse at 38% 50%,#5c4a40 0%,#2c2a2c 40%,#121316 70%,#0b0b0b 100%)}
.supp-title{left:700px;top:2725px;width:420px;text-align:center;font-size:46px;font-weight:700;color:var(--white)}
.supp-rule{left:896px;top:2802px;width:28px;height:3px;background:var(--white)}
.supp-text{left:740px;top:2817px;width:340px;text-align:center;color:var(--white);font-size:17px;line-height:35px}
.supp-btn{left:821px;top:2940px;width:178px;height:49px;font-size:17px;font-weight:500}

/* brands */
.brand{top:3245px;width:186px;height:108px;border:2px solid #d8d8d8;display:flex;align-items:center;justify-content:center;font-size:24px;font-weight:700;color:#333}
.brand.alt{background:#f4f4f4}
.arrow{top:3285px;width:40px;height:28px}

/* footer */
.footer-edge{left:0;top:3400px;width:1200px;height:648px;background:#5a5a5a;clip-path:polygon(0 118px,50% 0,100% 118px,100% 100%,0 100%)}
.footer{left:0;top:3412px;width:1200px;height:636px;clip-path:polygon(0 118px,50% 0,100% 118px,100% 100%,0 100%);
  background:radial-gradient(ellipse at 84% 40%,#3a3a3a 0%,#1a1a1a 35%,#000 65%)}
.pay{top:3594px;width:30px;height:18px;border-radius:2px}
.footer-logo{left:400px;top:3575px;width:400px;text-align:center;font-size:56px;color:var(--white)}
.contact-title{left:0;top:3670px;width:1200px;text-align:center;font-size:36px;color:var(--white)}
.social{top:3588px;width:34px;height:32px;background:#6a6a6a;border-radius:3px}
.col{top:3752px;width:300px;text-align:center;color:var(--white)}
.col svg{width:20px;height:20px;fill:#777}
.col h4{font-size:22px;font-weight:600;margin-top:20px;margin-bottom:12px}
.col p{font-size:13px;line-height:22px}
.divider{top:3757px;width:1px;height:131px;background:#444}
.bottom-rule{left:71px;top:3946px;width:1058px;height:1px;background:#3a3a3a}
.copyright{left:90px;top:3977px;color:#ddd;font-size:13px}
.legal{top:3977px;color:#ddd;font-size:13px;white-space:nowrap}
</style>
</head>
<body>
<div class="page">

  <!-- top bar -->
  <div class="abs topbar">
    <div class="item" style="left:100px"><svg viewBox="0 0 10 10"><path d="M5 0a3.5 3.5 0 0 0-3.5 3.5C1.5 6 5 10 5 10s3.5-4 3.5-6.5A3.5 3.5 0 0 0 5 0zm0 5a1.5 1.5 0 1 1 0-3 1.5 1.5 0 0 1 0 3z"/></svg>Store Location</div>
    <div class="sep" style="left:210px"></div>
    <div class="item" style="left:222px"><svg viewBox="0 0 12 10"><path d="M0 1h7v6H0zM7 3h3l2 2v2H7z"/><circle cx="2.5" cy="8.5" r="1.3"/><circle cx="9.5" cy="8.5" r="1.3"/></svg>Track Your Order</div>
    <div class="sep" style="left:357px"></div>
    <div class="item" style="left:368px"><svg viewBox="0 0 10 10"><circle cx="5" cy="3" r="2.5"/><path d="M0 10c0-3 2-4.5 5-4.5s5 1.5 5 4.5z"/></svg>Login / Register</div>
    <div class="sep" style="left:490px"></div>
    <div class="sep" style="left:810px"></div>
    <div class="item" style="left:820px"><svg viewBox="0 0 10 10"><path d="M2 0l2 2.5-1.2 1.3a6 6 0 0 0 3.4 3.4L7.5 6 10 8l-1.5 2C4 10 0 6 0 1.5z"/></svg>Hotline: +1 55 010 2468</div>
    <div class="sep" style="left:984px"></div>
    <div class="item" style="left:994px">English &#9662;</div>
    <div class="sep" style="left:1058px"></div>
    <div class="item" style="left:1068px">USD &#9662;</div>
  </div>

  <!-- header -->
  <svg class="abs crest" viewBox="0 0 200 133" aria-hidden="true"><polygon points="30,0 170,0 200,40 200,70 100,133 0,70 0,40" fill="#e8e8e8"/></svg>
  <div class="abs header-logo brandmark">VANTOR</div>
  <div class="abs search">
    <div class="round-icon"><svg viewBox="0 0 24 24"><circle cx="10" cy="10" r="6.5"/><path d="M15 15l6 6"/></svg></div>
    <div><b>SEARCH</b><span>Enter search here</span></div>
  </div>
  <div class="abs cart">
    <div class="round-icon"><svg viewBox="0 0 24 24"><path d="M2 4h3l2.5 11h11L21 7H7"/><circle cx="9" cy="19" r="1.4"/><circle cx="17" cy="19" r="1.4"/></svg></div>
    <div><b>MY CART</b>0 item - <strong>$0.00</strong></div>
  </div>

  <!-- nav -->
  <nav class="abs nav">
    <a style="left:146px">Protein</a>
    <a style="left:259px">Performance</a>
    <a style="left:420px">Weight Management</a>
    <a style="left:653px">Vitamins &amp; Health</a>
    <a style="left:860px">Clothing &amp; Accessories</a>
  </nav>

  <!-- hero -->
  <svg class="abs hero-edge" viewBox="0 0 1200 136" aria-hidden="true"><polygon points="0,13 600,128 1200,13 1200,20 600,136 0,20" fill="#555"/></svg>
  <div class="abs hero" role="img" aria-label="Woman in a grey hoodie lifting a barbell in a dim gym"></div>
  <div class="abs hero-logo brandmark">VANTOR</div>
  <p class="abs hero-text">Sed ut perspiciatis unde omnis iste natus error sit voluptatem accusanti</p>
  <div class="btn hero-btn">Get Started
    <svg width="17" height="17" viewBox="0 0 16 16"><circle cx="8" cy="8" r="8" fill="#fff"/><path d="M6 4.5L10 8l-4 3.5z" fill="#4d4d4d"/></svg>
  </div>
  <div class="abs dots"><i></i><i></i><i class="on"></i><i></i><i></i></div>

  <!-- features -->
  <div class="abs feature" style="left:75px">
    <div class="round-icon"><svg viewBox="0 0 24 24"><path d="M5 19l4-1 9-9c2-2 2-5 2-5s-3 0-5 2l-9 9zM6 14l-3 1 2-4h3M10 18l-1 3 4-2v-3"/></svg></div>
    <div><b>FREE SHIPPING</b><span>On Orders Over $49.00</span></div>
  </div>
  <div class="abs feature" style="left:342px">
    <div class="round-icon"><svg viewBox="0 0 24 24"><rect x="2" y="6" width="20" height="12" rx="2"/><circle cx="12" cy="12" r="3"/></svg></div>
    <div><b>MONEY GUARANTEE</b><span>30 days back</span></div>
  </div>
  <div class="abs feature" style="left:608px">
    <div class="round-icon"><svg viewBox="0 0 24 24"><rect x="2" y="5" width="20" height="14" rx="2"/><path d="M2 10h20M6 15h5"/></svg></div>
    <div><b>PAYMENT METHOD</b><span>Secure System</span></div>
  </div>
  <div class="abs feature" style="left:875px">
    <div class="round-icon"><svg viewBox="0 0 24 24"><path d="M4 15v-3a8 8 0 0 1 16 0v3"/><rect x="3" y="14" width="4" height="6" rx="1"/><rect x="17" y="14" width="4" height="6" rx="1"/></svg></div>
    <div><b>ONLINE SUPPORT</b><span>24 hours a day</span></div>
  </div>

  <!-- feature products -->
  <h2 class="abs section-title" style="top:986px">FEATURE PRODUCTS</h2>
  <div class="abs card" style="left:75px;top:1071px;background:radial-gradient(circle at 50% 45%,#c9c9c9 0%,#dedede 30%,#f5f5f5 55%)" role="img" aria-label="Light grey hoodie"></div>
  <div class="abs card" style="left:342px;top:1071px;background:radial-gradient(ellipse 30% 38% at 50% 48%,#111 0%,#222 85%,#f5f5f5 100%)" role="img" aria-label="Black supplement tub"></div>
  <div class="abs card" style="left:608px;top:1071px;background:radial-gradient(ellipse 42% 36% at 50% 47%,#1a1a1a 0%,#2a2a2a 80%,#f5f5f5 100%)" role="img" aria-label="Black zip hoodie"></div>
  <div class="abs card" style="left:875px;top:1071px;background:radial-gradient(ellipse 30% 38% at 50% 48%,#111 0%,#222 85%,#f5f5f5 100%)" role="img" aria-label="Black supplement tub"></div>
  <div class="abs card-name" style="left:75px;top:1440px">Grouped Product</div><div class="abs card-price" style="left:75px;top:1469px">$ 106.59</div>
  <div class="abs card-name" style="left:342px;top:1440px">Grouped Product</div><div class="abs card-price" style="left:342px;top:1469px">$ 106.59</div>
  <div class="abs card-name" style="left:608px;top:1440px">Grouped Product</div><div class="abs card-price" style="left:608px;top:1469px">$ 106.59</div>
  <div class="abs card-name" style="left:875px;top:1440px">Grouped Product</div><div class="abs card-price" style="left:875px;top:1469px">$ 106.59</div>

  <!-- apparel banner -->
  <div class="abs apparel" role="img" aria-label="Couple in grey t-shirts and jeans leaning on a concrete wall"></div>
  <div class="abs apparel-title">Apparel</div>
  <p class="abs apparel-text">Lorem ipsum dolor sit amet, consecte adipiscing elit, sed do eiusmod tempor incididunt ut labore et dolore magna aliqua.</p>
  <div class="btn apparel-btn">Shop Now</div>

  <!-- new arrivals -->
  <div class="abs arrivals-bg"></div>
  <h2 class="abs section-title" style="top:2078px">NEW ARRIVALS</h2>
  <div class="abs card" style="left:75px;top:2149px;background:radial-gradient(ellipse 34% 38% at 50% 48%,#111 0%,#222 85%,#f5f5f5 100%)" role="img" aria-label="Black supplement tub"></div>
  <div class="abs card" style="left:342px;top:2149px;background:radial-gradient(circle at 50% 45%,#c4c4c4 0%,#dadada 30%,#f5f5f5 55%)" role="img" aria-label="Light grey pullover hoodie"></div>
  <div class="abs card" style="left:608px;top:2149px;background:radial-gradient(ellipse 34% 38% at 50% 48%,#111 0%,#222 85%,#f5f5f5 100%)" role="img" aria-label="Black supplement tub"></div>
  <div class="abs card" style="left:875px;top:2149px;background:radial-gradient(ellipse 42% 38% at 50% 47%,#1e5fd0 0%,#2c6fe0 75%,#f5f5f5 100%)" role="img" aria-label="Blue zip hoodie"></div>
  <div class="abs card-name" style="left:75px;top:2518px">Grouped Product</div><div class="abs card-price" style="left:75px;top:2547px">$ 106.59</div>
  <div class="abs card-name" style="left:342px;top:2518px">Grouped Product</div><div class="abs card-price" style="left:342px;top:2547px">$ 106.59</div>
  <div class="abs card-name" style="left:608px;top:2518px">Grouped Product</div><div class="abs card-price" style="left:608px;top:2547px">$ 106.59</div>
  <div class="abs card-name" style="left:875px;top:2518px">Grouped Product</div><div class="abs card-price" style="left:875px;top:2547px">$ 106.59</div>

  <!-- supplement -->
  <div class="abs supplement"></div>
  <div class="abs supplement-photo" role="img" aria-label="Athlete with a towel drinking from an orange shaker bottle"></div>
  <div class="abs supp-title">Supplement</div>
  <div class="abs supp-rule"></div>
  <p class="abs supp-text">Lorem ipsum dolor sit amet, consectetur adipiscing elit, sed do labore et dolore magna aliqua.</p>
  <div class="btn supp-btn">New Arrivals</div>

  <!-- brands -->
  <h2 class="abs section-title" style="top:3168px">OUR BRAND</h2>
  <svg class="abs arrow" style="left:37px" viewBox="0 0 40 28" aria-hidden="true"><path d="M38 14H3M14 3L3 14l11 11" fill="none" stroke="#555" stroke-width="2.5"/></svg>
  <div class="abs brand" style="left:105px;font-weight:400;color:#666">Harrow Vale</div>
  <div class="abs brand" style="left:306px">MILLWORKS</div>
  <div class="abs brand" style="left:507px">BIG FELLOW</div>
  <div class="abs brand alt" style="left:708px">PIVOT</div>
  <div class="abs brand" style="left:909px">Quintra</div>
  <svg class="abs arrow" style="left:1123px" viewBox="0 0 40 28" aria-hidden="true"><path d="M2 14h35M26 3l11 11-11 11" fill="none" stroke="#555" stroke-width="2.5"/></svg>

  <!-- footer -->
  <div class="abs footer-edge"></div>
  <div class="abs footer" role="img" aria-label="Hooded athlete in shadow"></div>
  <div class="abs pay" style="left:90px;background:#e9e9e9"></div>
  <div class="abs pay" style="left:132px;background:#3b6fb6"></div>
  <div class="abs pay" style="left:174px;background:#f0f0f0"></div>
  <div class="abs pay" style="left:214px;background:#2c5aa8"></div>
  <div class="abs footer-logo brandmark">VANTOR</div>
  <div class="abs social" style="left:895px"></div>
  <div class="abs social" style="left:940px"></div>
  <div class="abs social" style="left:985px"></div>
  <div class="abs social" style="left:1030px"></div>
  <div class="abs social" style="left:1075px"></div>
  <h2 class="abs contact-title">CONTACT INFORMATIONS</h2>

  <div class="abs col" style="left:98px">
    <svg viewBox="0 0 10 10"><path d="M2 0l2 2.5-1.2 1.3a6 6 0 0 0 3.4 3.4L7.5 6 10 8l-1.5 2C4 10 0 6 0 1.5z"/></svg>
    <h4>CALL US</h4>
    <p>(+155)0 102 4680<br>(+155)0 102 4680</p>
  </div>
  <div class="abs divider" style="left:413px"></div>
  <div class="abs col" style="left:454px">
    <svg viewBox="0 0 10 10"><path d="M5 0L0 4.5h1.3V10h2.7V7h2v3h2.7V4.5H10z"/></svg>
    <h4>FIND US</h4>
    <p>No 18 Corven Street 214/6 Lakeport City,<br>LK, United States</p>
  </div>
  <div class="abs divider" style="left:766px"></div>
  <div class="abs col" style="left:807px">
    <svg viewBox="0 0 10 8"><path d="M0 0h10v1L5 4 0 1zM0 2l5 3 5-3v6H0z"/></svg>
    <h4>EMAIL</h4>
    <p>hello@vantorwear.com<br>care@vantorwear.com</p>
  </div>

  <div class="abs bottom-rule"></div>
  <div class="abs copyright">Vantor Wear and Fuel &copy; 2019. All Rights Reserved.</div>
  <div class="abs legal" style="left:623px">About</div>
  <div class="abs legal" style="left:689px">Legal information</div>
  <div class="abs legal" style="left:824px">Contact</div>
  <div class="abs legal" style="left:901px">Term of service</div>
  <div class="abs legal" style="left:1025px">Privacy policy</div>

</div>
</body>
</html>
```